KBT Business Cards

We require business cards for our business. We would like a matte black back to the card, with our logo centred in the middle. The front side of the card is open to design.

Target Market(s)

Clients looking for legal services (professional)

Industry/Entity Type

Legal

Contact Information for Business Card

Doran Kelbrath
Partner
Mobile: 0461 738 524
Email: doran@kbtlaw.co
Website: www.kbtlaw.co
Level 3, 118 Wendmore Street
Sydney NSW 2000

Font styles to use
Other font styles liked:
• Avenir

Colors
f04a50
ffffff
1b1b1b

Requirements
Must have
• Black back with logo included in the centre of the card.
• Our font is Avenir.

```html
<!DOCTYPE html>
<html lang="en">
<head>
<meta charset="utf-8">
<title>KBT Business Cards</title>
<link href="https://fonts.googleapis.com/css2?family=Nunito+Sans:wght@300;400;600;800&display=swap" rel="stylesheet">
<style>
  :root {
    --brand-red: #c8193f;
    --brand-red-deep: #a8163a;
    --ink: #1b1b1b;
    --black: #0c0c0c;
    --paper: #ffffff;
    --stage: #e9e9ea;
    --card-w: 640px;
    --card-h: 391px;
  }
  * { box-sizing: border-box; margin: 0; padding: 0; }
  html, body {
    width: 1200px; height: 960px; overflow: hidden;
    background: var(--stage);
    font-family: "Nunito Sans", "Avenir", sans-serif;
  }
  .sheet {
    width: 1200px; height: 960px;
    display: flex; flex-direction: column; align-items: center; justify-content: center;
    gap: 60px;
  }
  .card {
    position: relative;
    width: var(--card-w); height: var(--card-h);
    overflow: hidden;
    box-shadow: 0 6px 20px rgba(0,0,0,.15);
  }

  /* ---------- Back ---------- */
  .card--back { background: var(--ink); }
  .back-brand {
    position: absolute; left: 0; right: 0; top: 118px;
    display: flex; align-items: center; justify-content: center; gap: 22px;
  }
  .brand-square { width: 62px; height: 62px; background: var(--brand-red); flex: none; }
  .brand-name {
    font-weight: 800; text-transform: uppercase;
    line-height: 1.0; letter-spacing: .5px;
  }
  .card--back .brand-name { color: var(--paper); font-size: 28px; }
  .back-url {
    position: absolute; left: 0; right: 0; top: 298px;
    text-align: center; font-size: 14px; letter-spacing: 4px;
    color: var(--paper); font-weight: 400;
  }
  .back-url .accent { color: var(--brand-red); font-weight: 600; }

  /* ---------- Front ---------- */
  .card--front { background: var(--paper); }
  .front-brand {
    position: absolute; left: 32px; top: 30px;
    display: flex; align-items: flex-start; gap: 18px;
  }
  .front-brand .brand-square { width: 56px; height: 56px; }
  .card--front .brand-name { color: var(--ink); font-size: 24px; margin-top: 42px; }

  .name-band {
    position: absolute; left: 0; top: 160px; width: 382px; height: 66px;
    background: linear-gradient(90deg, var(--brand-red-deep), var(--brand-red));
    padding: 10px 0 0 32px; color: var(--paper);
  }
  .person-name { font-size: 21px; font-weight: 800; text-transform: uppercase; letter-spacing: .5px; line-height: 1.1; }
  .person-role { font-size: 13px; font-weight: 300; text-transform: uppercase; letter-spacing: 1px; }

  .contact-block {
    position: absolute; left: 382px; top: 214px; right: 0; height: 120px;
    background: var(--black);
  }
  .icon-strip {
    position: absolute; left: 350px; top: 214px; width: 32px; height: 88px;
    background: var(--brand-red);
    display: flex; flex-direction: column; align-items: center; justify-content: space-around;
    padding: 4px 0;
  }
  .icon-strip svg { width: 15px; height: 15px; }
  .contact-list {
    position: absolute; left: 398px; top: 222px;
    list-style: none; color: var(--paper); font-size: 15px; line-height: 26px; font-weight: 400;
  }
  .address {
    position: absolute; left: 32px; top: 252px; width: 308px;
    font-size: 13px; color: var(--ink); font-weight: 400; line-height: 1.4;
    white-space: nowrap;
  }
</style>
</head>
<body>
<main class="sheet">

  <section class="card card--back" aria-label="Card back">
    <div class="back-brand">
      <span class="brand-square"></span>
      <div class="brand-name">Kelbrath<br>Bane<br>Tolliver</div>
    </div>
    <p class="back-url">www.<span class="accent">kbtlaw</span>.co</p>
  </section>

  <section class="card card--front" aria-label="Card front">
    <div class="front-brand">
      <span class="brand-square"></span>
      <div class="brand-name">Kelbrath<br>Bane<br>Tolliver</div>
    </div>

    <div class="name-band">
      <p class="person-name">Doran Kelbrath</p>
      <p class="person-role">Partner</p>
    </div>

    <p class="address">Level 3, 118 Wendmore Street, Sydney NSW 2000</p>

    <div class="contact-block"></div>
    <div class="icon-strip">
      <svg viewBox="0 0 16 16" aria-label="Phone" role="img"><rect x="4" y="1" width="8" height="14" rx="1.5" fill="none" stroke="#fff" stroke-width="1.4"/><circle cx="8" cy="12.3" r=".9" fill="#fff"/></svg>
      <svg viewBox="0 0 16 16" aria-label="Email" role="img"><rect x="1.5" y="3.5" width="13" height="9" fill="none" stroke="#fff" stroke-width="1.4"/><path d="M1.5 3.5 8 9l6.5-5.5" fill="none" stroke="#fff" stroke-width="1.4"/></svg>
      <svg viewBox="0 0 16 16" aria-label="Website" role="img"><circle cx="8" cy="8" r="6.3" fill="none" stroke="#fff" stroke-width="1.3"/><ellipse cx="8" cy="8" rx="2.8" ry="6.3" fill="none" stroke="#fff" stroke-width="1.1"/><path d="M1.7 8h12.6M2.8 4.8h10.4M2.8 11.2h10.4" stroke="#fff" stroke-width="1"/></svg>
    </div>
    <ul class="contact-list">
      <li>0461 738 524</li>
      <li>doran@kbtlaw.co</li>
      <li>www.kbtlaw.co</li>
    </ul>
  </section>

</main>
</body>
</html>
```